Professional Website

We are looking for a new website for our Staffing Company. Attached is a document with all the details and pages needed along with some examples of others websites.

We want a professional Look and feel around the same color theme as the attached Amber Compass.

We currently host our site on PageLoom.io. If the winning designer can also add to PageLoom, that is a plus.

```html
<!DOCTYPE html>
<html lang="en">
<head>
<meta charset="utf-8">
<title>CrewBridge Clerical &amp; Industrial</title>
<link href="https://fonts.googleapis.com/css2?family=Montserrat:wght@800&family=Roboto:wght@400;500;700&display=swap" rel="stylesheet">
<style>
:root{
  --blue:#2b2e93;
  --ink:#1c1c1c;
  --grey-text:#7a7a7a;
  --panel:rgba(110,110,110,.82);
  --soft:#f4f4f4;
  --footer:#161616;
  --white:#ffffff;
}
*{margin:0;padding:0;box-sizing:border-box}
html,body{width:687px;height:1200px;overflow:hidden;background:var(--white)}
body{font-family:"Roboto",sans-serif;color:var(--ink);position:relative}
.abs{position:absolute}

/* header */
.menu-toggle{left:64px;top:22px;width:12px;height:10px;display:flex;flex-direction:column;justify-content:space-between}
.menu-toggle span{height:2px;background:var(--ink)}
.call-badge{left:94px;top:14px;width:27px;height:27px;border-radius:50%;background:var(--white);box-shadow:0 1px 5px rgba(0,0,0,.18);display:flex;align-items:center;justify-content:center}
.hotline{left:133px;top:22px;font-size:8.5px;font-weight:500;color:var(--ink)}
.hotline b{color:var(--blue);font-weight:500}
.brand{left:289px;top:15px;display:flex;align-items:center;gap:4px;font-size:18px;font-weight:700;color:var(--blue);letter-spacing:-.3px}
.brand i{width:9px;height:9px;background:var(--blue);display:block}
.top-links{right:64px;top:22px;display:flex;font-size:6.6px;font-weight:700;color:var(--ink)}
.top-links a{color:inherit;text-decoration:none;padding:0 7px;border-left:1px solid #ddd;line-height:10px}
.top-links a:first-child{border-left:0}
.top-links a:last-child{padding-right:0}

/* hero */
.hero-photo{left:0;top:54px;width:687px;height:378px;background:linear-gradient(100deg,#d9dcdf 0%,#b9bec3 35%,#c7b8a8 60%,#8b8f96 85%,#6c7078 100%)}
.hero-shape{left:0;top:54px}
.hero-panel{left:64px;top:141px;width:304px;height:169px;background:var(--panel);padding:18px 16px}
.hero-title{font-family:"Montserrat",sans-serif;font-weight:800;font-size:20.5px;line-height:27px;color:var(--white)}
.hero-lede{margin-top:9px;font-size:8.8px;line-height:14.7px;color:var(--white);font-weight:500}
.btn{display:inline-flex;align-items:center;justify-content:center;background:var(--blue);color:var(--white);font-size:8px;font-weight:700;height:29px}
.hero-panel .btn{margin-top:15px;width:79px}

/* audience cards */
.card{top:467px;width:275px;height:216px;background:var(--white);box-shadow:0 1px 6px rgba(0,0,0,.12);padding:4px}
.card-photo{height:163px}
.card-icon{position:absolute;left:50%;top:137px;margin-left:-24px;width:48px;height:48px;border-radius:50%;background:var(--blue);border:3px solid var(--white);display:flex;align-items:center;justify-content:center}
.card-label{text-align:center;margin-top:22px;font-size:11.3px;font-weight:500;color:var(--ink);letter-spacing:.1px}
.card-job{left:64px}
.card-job .card-photo{background:linear-gradient(110deg,#4b525a 0%,#8a9097 40%,#b6bcc2 70%,#6f8796 100%)}
.card-hire{left:348px}
.card-hire .card-photo{background:linear-gradient(110deg,#d8dadc 0%,#c9b9a6 45%,#b7b9bb 70%,#2e4868 100%)}

/* about */
.about-bg{left:0;top:715px;width:687px;height:360px}
.about-photo{left:64px;top:823px;width:280px;height:206px;background:linear-gradient(110deg,#c5cbd0 0%,#8c97a3 35%,#2f4460 60%,#3b4e69 100%)}
.about-copy{left:377px;top:836px;width:246px}
.about-title{font-family:"Montserrat",sans-serif;font-weight:800;font-size:19px;color:var(--ink)}
.about-title em{font-style:normal;color:var(--blue)}
.about-text{margin-top:18px;font-size:8.1px;line-height:14.7px;color:var(--grey-text);text-align:justify}
.about-copy .btn{margin-top:22px;width:71px}

/* footer */
.site-footer{left:0;top:1075px;width:687px;height:125px;background:var(--footer);color:var(--white)}
.footer-brand{left:64px;top:32px;display:flex;align-items:center;gap:6px;font-size:26px;font-weight:700;letter-spacing:-.5px}
.footer-brand i{width:13px;height:13px;background:var(--white);display:block}
.branches{right:64px;top:32px;display:flex;gap:18px;font-size:11px;font-weight:700}
.branches span.sep{font-weight:400}
.footer-hotline{right:64px;top:54px;font-size:9.6px;font-weight:500}
.footer-rule{left:64px;top:91px;width:559px;height:1px;background:#3a3a3a}
.copyright{left:0;top:100px;width:687px;text-align:center;font-size:8px}
</style>
</head>
<body>

<header>
  <div class="abs menu-toggle" aria-label="Menu"><span></span><span></span><span></span></div>
  <div class="abs call-badge">
    <svg width="12" height="12" viewBox="0 0 24 24" fill="none" stroke="#2b2e93" stroke-width="2.4" stroke-linecap="round"><path d="M5 3l4 1 1 5-2 2a12 12 0 0 0 5 5l2-2 5 1 1 4-3 2C10 21 3 14 3 6z" fill="#2b2e93"/><path d="M15 3a6 6 0 0 1 6 6"/><path d="M14 7a3 3 0 0 1 3 3"/></svg>
  </div>
  <div class="abs hotline"><b>HOTLINE:</b> 555-014-2290</div>
  <div class="abs brand"><i></i>CrewBridge</div>
  <nav class="abs top-links">
    <a href="#">EMPLOYEE LOGIN</a>
    <a href="#">PAYCARD LOGIN</a>
    <a href="#">HARBOR BANK LOGIN</a>
  </nav>
</header>

<section>
  <div class="abs hero-photo" role="img" aria-label="Photo of two smiling professional women talking across an office desk"></div>
  <svg class="abs hero-shape" width="687" height="378" viewBox="0 0 687 378">
    <polygon points="0,290 457,366 687,290 687,294 457,378 0,292" fill="#2b2e93"/>
    <polygon points="0,292 457,378 687,294 687,378 0,378" fill="#ffffff"/>
  </svg>
  <div class="abs hero-panel">
    <h1 class="hero-title">CREWBRIDGE CLERICAL<br>AND INDUSTRIAL</h1>
    <p class="hero-lede">To change the way temporary staffing agencies fill orders.&nbsp; We only work with the best companies and best employees.</p>
    <a class="btn" href="#">GET STARTED</a>
  </div>
</section>

<section>
  <div class="abs card card-job">
    <div class="card-photo" role="img" aria-label="Photo of a job candidate shaking hands with an interviewer"></div>
    <div class="card-icon">
      <svg width="24" height="24" viewBox="0 0 24 24" fill="none" stroke="#fff" stroke-width="1.2"><circle cx="9" cy="6" r="3"/><path d="M3 22v-6a6 6 0 0 1 12 0"/><rect x="12" y="15" width="9" height="6"/><path d="M15 15v-2h3v2"/></svg>
    </div>
    <p class="card-label">I’M LOOKING FOR A JOB</p>
  </div>
  <div class="abs card card-hire">
    <div class="card-photo" role="img" aria-label="Photo of a team meeting around a table with laptops"></div>
    <div class="card-icon">
      <svg width="24" height="24" viewBox="0 0 24 24" fill="none" stroke="#fff" stroke-width="1.2"><circle cx="12" cy="9" r="2.5"/><circle cx="6" cy="14" r="2"/><circle cx="18" cy="14" r="2"/><path d="M2 21a4 4 0 0 1 8 0M14 21a4 4 0 0 1 8 0M8 17a4 4 0 0 1 8 0"/><path d="M6 6a7 7 0 0 1 12 0"/></svg>
    </div>
    <p class="card-label">I NEED EMPLOYEES</p>
  </div>
</section>

<section>
  <svg class="abs about-bg" width="687" height="360" viewBox="0 715 687 360">
    <polygon points="0,808 230,721 687,808 687,811 230,731 0,810" fill="#2b2e93"/>
    <polygon points="0,810 230,731 687,811 687,1075 0,1075" fill="#f4f4f4"/>
  </svg>
  <div class="abs about-photo" role="img" aria-label="Photo of a recruiter reviewing a résumé with a candidate"></div>
  <div class="abs about-copy">
    <h2 class="about-title">ABOUT <em>US</em></h2>
    <p class="about-text">Greatest part of our daily job is that we are constantly bringing people together. Our Clients come to us in search of the perfect candidate and the job hunters approach us when they are in need of a job or looking for their next exciting role. Being able to work with and connect the two is incredibly satisfying. Not to mention that in today's current job market</p>
    <a class="btn" href="#">READ MORE</a>
  </div>
</section>

<footer class="abs site-footer">
  <div class="abs footer-brand"><i></i>CrewBridge</div>
  <div class="abs branches"><span>LAKEVIEW</span><span class="sep">|</span><span>OAK HOLLOW</span><span class="sep">|</span><span>RIVERBEND</span></div>
  <div class="abs footer-hotline">Hotline: 555-014-2290</div>
  <div class="abs footer-rule"></div>
  <p class="abs copyright">© 2022 CrewBridge&nbsp; |&nbsp; All Rights Reserved</p>
</footer>

</body>
</html>
```